Thoroughbred Racing Partnership needs web design

Glimmer of Laurel Partners is a management group who buys horses and races them on both the West and East coasts. The premise of the business is for an investment as little as $500, anyone can be a partner and own a percentage of a horse(s). This is a low cost way of getting involved in the exciting sport of Thoroughbred Racing, without shouldering the heavy financial responsibility. Our target market is mostly males 40+ but we want to include all target markets. We are looking for something very clean and professional, we want to give an image of success. Nothing overly "artsy." I have included the logo in which you can incorporate in the site. Also, the logo colors will be the colors of our "silks." The silks are what the jockey wears and will be an important marketing tool for GOL. We would like a very prominent picture of a racehorse somewhere on the homepage, we want to make it clear that is a website for Horseracing partnerships.

On the top of the site, it should say "Glimmer of Laurel" (on the top)
and below that "Thoroughbred Racing Partnerships." (below that)

The main sections, which should be across the top are:

Home
About Us
Ownership
Stable Roster
News
Contact us

Some of these will have drop down menus.

An example of a competitor website that we like is: www.harrowgatefarm.example
An example of a competitor website that we don't like is: www.paddockvue.example
Updates

Project Deadline Extended
Reason: We have a Board of Directors meeting on the 22nd and we will be making a decision on that day. I'm giving an extension so that all designers are able to submit their designs by the 22nd. Thank you!

Target Market(s)

40+ males

Industry/Entity Type

Business

Requirements
Must have
• our logo must be on the site. We would like at least one bold image of a thoroughbred horse in action. The picture is going to tell the story so it needs to be very eye-catching.

Our slogan should also be included on the website, "Experience the thrill of owning a Racehorse."
Should not have
• cartoons, artsy pictures, pictures of Steeplechase horses or "jumpers." This partnership is for racehorses only, there is not jumping involved with the horses.

```html
<!DOCTYPE html>
<html lang="en">
<head>
<meta charset="utf-8">
<title>Glimmer of Laurel Partners – Thoroughbred Racing Partnerships</title>
<link rel="stylesheet" href="https://fonts.googleapis.com/css2?family=Source+Sans+3:ital,wght@0,400;0,600;0,700;1,600;1,700&family=Oswald:wght@500&family=Fira+Sans+Condensed:wght@500&display=swap">
<style>
:root{
  --navy:#0b4d82;
  --navy-deep:#04365f;
  --ink:#4a4a4a;
  --rule:#cfcfcf;
  --page:#ffffff;
  --white:#ffffff;
}
*{box-sizing:border-box;margin:0;padding:0}
html,body{width:1200px;height:1102px;overflow:hidden}
body{position:relative;font-family:"Source Sans 3",sans-serif;color:var(--ink);
  background:linear-gradient(180deg,#b9bdc0 0%,#8f9599 45%,#a6abae 100%)}
.backdrop{position:absolute;inset:0 0 167px 0;
  background:radial-gradient(ellipse at 8% 45%,#6f767a 0%,rgba(0,0,0,0) 45%),radial-gradient(ellipse at 94% 40%,#767c80 0%,rgba(0,0,0,0) 45%)}
.page{position:absolute;left:131px;top:0;width:938px;height:935px;background:var(--page)}
.abs{position:absolute}

/* header */
.logo{left:10px;top:14px;width:230px}
.logo-name{font-weight:700;color:var(--navy);font-size:52px;line-height:48px;letter-spacing:1px}
.logo-site{font-weight:700;color:var(--navy);font-size:22px;line-height:28px;letter-spacing:.5px}
.tagline{left:480px;top:18px;width:260px;text-align:center;font-family:"Fira Sans Condensed",sans-serif;font-weight:500;color:#4a7aa6;font-size:16px;line-height:21px;white-space:nowrap}
.call{left:760px;top:21px}
.call-icon{position:absolute;left:0;top:0;width:33px;height:33px;border-radius:7px;background:linear-gradient(#f4f4f4,#d8d8d8);border:1px solid #d0d0d0}
.call-label{position:absolute;left:44px;top:0;font-weight:600;font-size:13px;color:#333;white-space:nowrap}
.call-num{position:absolute;left:43px;top:14px;font-family:"Fira Sans Condensed",sans-serif;font-weight:500;font-size:20px;color:var(--navy);white-space:nowrap}

.nav{left:281px;top:77px;width:647px;height:37px;background:var(--navy);display:flex}
.nav a{display:block;height:37px;line-height:37px;color:var(--white);text-decoration:none;font-weight:600;font-size:14.5px;text-align:center;border-left:1px solid #2d6b9d}
.nav a:first-child{border-left:0}
.nav a.current{background:#000}

/* hero */
.hero{left:10px;top:121px;width:919px;height:431px;
  background:linear-gradient(180deg,#3e5a2c 0%,#4f6e34 30%,#a9b9a0 55%,#6e9a3a 68%,#7aa847 100%)}
.hero-band{position:absolute;left:0;top:366px;width:919px;height:56px;background:rgba(20,20,20,.72)}
.slogan{position:absolute;left:15px;top:5px;font-family:"Oswald",sans-serif;font-weight:500;font-size:31px;color:var(--white);letter-spacing:-.3px;text-shadow:1px 1px 2px #000}
.dots{position:absolute;right:18px;top:19px;display:flex;gap:7px}
.dots span{width:18px;height:18px;background:var(--white);border:1px solid #ccc}
.dots span.on{background:#3d79aa;border-color:#2f6594}

/* welcome */
.section-title{font-weight:600;font-size:23px;color:var(--navy)}
.welcome{left:10px;top:569px;width:592px}
.welcome .section-title{padding-bottom:6px;border-bottom:1px solid var(--rule)}
.photo-frame{position:absolute;left:0;top:43px;width:188px;height:143px;border:1px solid var(--rule);padding:4px;background:#fff}
.photo{width:100%;height:100%;background:linear-gradient(160deg,#2a2118 0%,#5b4a3a 50%,#1c1a18 100%)}
.welcome-text{position:absolute;left:198px;top:42px;width:394px;font-size:12.6px;line-height:21px;letter-spacing:.15px;text-align:justify}
.more{position:absolute;font-weight:700;font-size:13px;color:var(--navy);text-decoration:none}
.welcome .more{right:4px;top:174px}

.vdivider{left:621px;top:611px;width:1px;height:120px;background:var(--rule)}

.news{left:642px;top:569px;width:277px}
.news .section-title{padding-bottom:6px;border-bottom:1px solid var(--rule)}
.news-item{position:absolute;left:6px;width:272px;height:72px}
.date{position:absolute;left:0;top:0;width:40px;height:43px;background:#e6e6e6;text-align:center}
.date b{display:block;height:29px;line-height:31px;font-weight:600;font-size:20px;color:#333}
.date i{display:block;height:14px;line-height:14px;font-style:normal;font-weight:700;font-size:10px;color:var(--white);background:var(--navy)}
.news-body{position:absolute;left:53px;top:0;width:218px;font-size:12.4px;line-height:18px}
.news-body strong{display:block;font-weight:700;color:#333}
.news .more{right:2px;top:183px}

.hrule{left:10px;top:786px;width:919px;height:1px;background:var(--rule)}

/* testimonials */
.testimonials{left:10px;top:817px;width:919px;height:88px;border:1px solid var(--rule);border-radius:4px}
.testimonials svg{position:absolute;left:2px;top:2px}
.t-label{position:absolute;left:14px;top:22px;width:140px;text-align:center;font-weight:600;font-size:19px;line-height:21px;color:var(--white)}
.quote{position:absolute;top:13px;width:320px;font-size:12.8px;line-height:18.5px;letter-spacing:.1px}
.quote .mark{font-family:Georgia,serif;font-size:30px;line-height:10px;color:#c8c8c8;vertical-align:-10px;margin-left:-13px;margin-right:3px}
.quote cite{display:block;text-align:right;font-weight:700;font-style:italic;color:#333;margin-top:-6px}
.q-divider{position:absolute;left:548px;top:10px;width:0;height:68px;border-left:1px dashed var(--rule)}

/* footer */
.footer{position:absolute;left:0;top:935px;width:1200px;height:167px;background:linear-gradient(180deg,var(--navy) 0%,var(--navy-deep) 100%);border-top:2px solid #1f6aa6;color:var(--white)}
.f-col{position:absolute;top:16px}
.f-col h3{font-weight:600;font-size:18px;letter-spacing:.6px;padding-bottom:6px;border-bottom:1px solid #3b77a8}
.f-sep{position:absolute;top:20px;width:1px;height:135px;background:linear-gradient(#1f5f95,#0c3e67)}
.links{list-style:none;display:grid;grid-template-columns:87px 80px;row-gap:6px;margin-top:11px;font-size:12.8px}
.links li::before{content:"»";font-size:9px;color:#9fc1de;margin-right:5px;vertical-align:2px}
.links li.blank::before{content:none}
.f-text{font-size:12.8px;line-height:17px}
.email-field{width:185px;height:24px;border:1px solid #9db6cc;border-radius:3px;background:#fff;color:#666;font-size:11.5px;line-height:22px;padding-left:9px}
.subscribe{display:inline-block;padding:0 9px;height:24px;line-height:24px;background:#063563;border:1px solid #1a5a90;border-radius:2px;font-weight:700;font-size:13px}
.c-row{position:relative;padding-left:24px;font-size:12.8px;line-height:18.5px}
.c-row svg{position:absolute;left:0;top:2px}
.social{display:flex;gap:7px;justify-content:center;margin-top:19px}
.social span{width:28px;height:28px;border-radius:4px}
</style>
</head>
<body>
<div class="backdrop" role="img" aria-label="Blurred grey photograph of racehorses and jockeys running"></div>

<div class="page">
  <div class="abs logo">
    <div class="logo-name">GOL</div>
    <div class="logo-site">GOLPARTNERS.COM</div>
  </div>
  <div class="abs tagline">Glimmer of Laurel<br>Thoroughbred Racing Partnerships</div>
  <div class="abs call">
    <div class="call-icon">
      <svg width="33" height="33" viewBox="0 0 33 33"><path d="M11 8c1-1 2.5-1 3 .3l1.6 3.2c.4.9 0 1.7-.7 2.2l-1.3.9c.8 2.3 2.6 4.3 4.9 5.3l1-1.2c.6-.7 1.5-.9 2.3-.4l3 1.8c1.1.7 1 2 .1 2.9l-1.6 1.6c-5.8 1.2-13.5-6.7-12.8-13z" fill="#444"/></svg>
    </div>
    <div class="call-label">Call Us:</div>
    <div class="call-num">(555) 014-2286</div>
  </div>
  <nav class="abs nav">
    <a class="current" style="width:85px">Home</a>
    <a style="width:108px">About Us</a>
    <a style="width:115px">Ownership</a>
    <a style="width:138px">Stable Roster</a>
    <a style="width:86px">News</a>
    <a style="width:115px">Contact us</a>
  </nav>

  <div class="abs hero" role="img" aria-label="Photograph of two thoroughbred racehorses with jockeys galloping on a grass track beside a white rail">
    <div class="hero-band">
      <div class="slogan">Experience the thrill of owning a Racehorse.</div>
      <div class="dots"><span class="on"></span><span></span><span></span><span></span></div>
    </div>
  </div>

  <section class="abs welcome">
    <h2 class="section-title">Welcome to GOL Partners</h2>
    <div class="photo-frame"><div class="photo" role="img" aria-label="Photograph of partners presenting a framed award"></div></div>
    <p class="welcome-text">Glimmer of Laurel Partners is a management group who buys horses and races them on both the West and East coasts. The premise of the business is for an investment as little as $500, anyone can be a partner and own a percentage of a horse(s). This is a low cost way of getting involved in the exciting sport of Thoroughbred Racing, without shouldering the heavy financial responsibility.</p>
    <a class="more">Read More »</a>
  </section>

  <div class="abs vdivider"></div>

  <section class="abs news">
    <h2 class="section-title">Latest News</h2>
    <div class="news-item" style="top:44px;border-bottom:1px dotted var(--rule)">
      <div class="date"><b>26</b><i>MAR</i></div>
      <div class="news-body"><strong>Duis aute irure dolor in reprehen</strong>voluptate velit esse cillum fugiat nulla pariatur. Excepteur sint occaecat..</div>
    </div>
    <div class="news-item" style="top:115px">
      <div class="date"><b>27</b><i>MAR</i></div>
      <div class="news-body"><strong>Duis aute irure dolor in reprehen</strong>voluptate velit esse cillum fugiat nulla pariatur. Excepteur sint occaecat..</div>
    </div>
    <a class="more">Read More »</a>
  </section>

  <div class="abs hrule"></div>

  <section class="abs testimonials">
    <svg width="170" height="83" viewBox="0 0 170 83"><defs><linearGradient id="tg" x1="0" y1="0" x2="0" y2="1"><stop offset="0" stop-color="#0f5a94"/><stop offset="1" stop-color="#074275"/></linearGradient></defs><path d="M4 0H150L170 41.5 150 83H4a4 4 0 0 1-4-4V4a4 4 0 0 1 4-4z" fill="url(#tg)"/></svg>
    <div class="t-label">Client<br>Testimonials</div>
    <div class="quote" style="left:210px"><span class="mark">“</span>Sed diam nonummy nibh euismod tincidunt ut laoreet dolore magna aliquam erat volutpat. Ut wisi enim a mini veniam, quis nostrud exerci tation<cite>- Aliquam erat</cite></div>
    <div class="q-divider"></div>
    <div class="quote" style="left:580px"><span class="mark">“</span>Sed diam nonummy nibh euismod tincidunt ut laoreet dolore magna aliquam erat volutpat. Ut wisi enim a mini veniam, quis nostrud exerci tation<cite>- Aliquam erat</cite></div>
  </section>
</div>

<footer class="footer">
  <div class="f-col" style="left:140px;width:156px">
    <h3>Quick Links</h3>
    <ul class="links"><li>Home</li><li>News</li><li>About Us</li><li>Contact us</li><li>Ownership</li><li class="blank"></li><li>Stable Roster</li></ul>
  </div>
  <div class="f-sep" style="left:321px"></div>
  <div class="f-col" style="left:352px;width:200px">
    <h3 style="border:0">Newsletter</h3>
    <p class="f-text" style="margin:4px 0 11px 1px">Get the latest updates by entering your email address</p>
    <div class="email-field">Email Address</div>
    <div class="subscribe" style="margin-top:11px">Subscribe</div>
  </div>
  <div class="f-sep" style="left:568px"></div>
  <div class="f-col" style="left:605px;width:218px">
    <h3>Contact Details</h3>
    <div class="c-row" style="margin-top:10px"><svg width="12" height="18" viewBox="0 0 12 18"><path d="M6 0a6 6 0 0 1 6 6c0 4-6 12-6 12S0 10 0 6a6 6 0 0 1 6-6z" fill="#fff"/><circle cx="6" cy="6" r="2.2" fill="#0b4d82"/></svg>Lorem ipsum dolor sit consectetur adipiscing elit.site amet</div>
    <div class="c-row" style="margin-top:8px"><svg width="14" height="14" viewBox="0 0 14 14"><path d="M2.5 1c.7-.6 1.6-.5 2 .3l1 2c.3.6 0 1.2-.5 1.5l-.8.5c.5 1.5 1.7 2.8 3.2 3.4l.6-.7c.4-.5 1-.6 1.5-.3l2 1.2c.7.4.7 1.3.1 1.9l-1 1C6.8 12.5 1.6 7.3 2.5 1z" fill="#fff"/></svg>(555) 014-2286</div>
    <div class="c-row" style="margin-top:6px"><svg width="16" height="12" viewBox="0 0 16 12"><rect x=".5" y=".5" width="15" height="11" fill="#fff"/><path d="M.5.5 8 7 15.5.5" fill="none" stroke="#0b4d82" stroke-width="1.3"/></svg>info@golpartners.example</div>
  </div>
  <div class="f-sep" style="left:850px"></div>
  <div class="f-col" style="left:881px;width:180px">
    <h3>Follow Us</h3>
    <div class="social">
      <span style="background:#3b5fa6" role="img" aria-label="Social profile link"></span>
      <span style="background:#47a9e0" role="img" aria-label="Social profile link"></span>
      <span style="background:#d9483a" role="img" aria-label="Social profile link"></span>
      <span style="background:#cb2027" role="img" aria-label="Social profile link"></span>
    </div>
    <p class="f-text" style="text-align:center;margin-top:13px;line-height:20px">Copyright © 2013 Golpartners<br>All Rights Reserved</p>
  </div>
</footer>
</body>
</html>
```